Design a (20.4 x 10.14) Banner that says - Keep Hope Rising From Corvalis TV Family

We want a design (20.4 x 10.14) with the words 'Keep Hope Rising' as the main text and 'From Corvalis TV Family' underneath. For 'Corvalis TV', we'd like you to use the logo which can be found in the image attached.

The image attached is just an example but please let your creative juices flow!

Target Market(s)

Christian

Industry/Entity Type

Christian

Requirements
Must have
• Must have the words 'Keep Hope Rising' and 'From Corvalis TV Family'.

```html
<!DOCTYPE html>
<html lang="en">
<head>
<meta charset="utf-8">
<title>Keep Hope Rising – From Corvalis TV Family</title>
<link href="https://fonts.googleapis.com/css2?family=Great+Vibes&family=Montserrat:wght@400;600;700;800&display=swap" rel="stylesheet">
<style>
  :root {
    --cyan-deep: #1cc4e6;
    --cyan-light: #62e3f2;
    --photo-dark: #5f7ea6;
    --photo-mid: #8eaccb;
    --photo-light: #c4d6e6;
    --white: #ffffff;
    --accent: #39d9ee;
    --accent-light: #8cf0f8;
    --ink: #353c96;
  }
  * { margin: 0; padding: 0; box-sizing: border-box; }
  html, body { width: 1200px; height: 596px; overflow: hidden; }
  body { background: var(--white); font-family: "Montserrat", sans-serif; }

  .banner {
    position: relative;
    width: 1200px;
    height: 596px;
    overflow: hidden;
    background: linear-gradient(120deg, var(--cyan-deep) 0%, var(--cyan-light) 100%);
  }
  .banner__shape { position: absolute; inset: 0; }

  .headline {
    position: absolute;
    left: 240px;
    top: 206px;
  }
  .headline__script {
    display: block;
    font-family: "Great Vibes", cursive;
    font-size: 84px;
    line-height: 1;
    color: var(--accent);
    margin-left: -10px;
  }
  .headline__main {
    display: flex;
    align-items: center;
    margin-top: -18px;
    font-weight: 600;
    font-size: 82px;
    letter-spacing: 17px;
    line-height: 1;
  }
  .headline__white { color: var(--white); }
  .headline__accent {
    background: linear-gradient(90deg, var(--accent) 0%, var(--accent-light) 100%);
    -webkit-background-clip: text;
    background-clip: text;
    color: transparent;
  }
  .headline__chevrons { margin-left: 2px; }

  .signoff {
    position: absolute;
    left: 428px;
    top: 386px;
    width: 344px;
    height: 76px;
    border-radius: 38px;
    background: var(--white);
    box-shadow: 0 4px 14px rgba(20, 60, 110, .25);
    display: flex;
    align-items: center;
    justify-content: center;
  }
  .signoff__text {
    font-weight: 700;
    font-size: 21px;
    letter-spacing: 1px;
    color: var(--ink);
    white-space: nowrap;
  }
</style>
</head>
<body>
<main class="banner">
  <svg class="banner__shape" width="1200" height="596" viewBox="0 0 1200 596">
    <defs>
      <linearGradient id="photoTone" x1="0" y1="0" x2="1" y2="1">
        <stop offset="0" stop-color="#5f7ea6"/>
        <stop offset=".55" stop-color="#8eaccb"/>
        <stop offset="1" stop-color="#c4d6e6"/>
      </linearGradient>
    </defs>
    <path role="img" aria-label="Blue-toned photo of a shepherd holding a white lamb in his arms"
          d="M0 300 C 100 170 230 60 372 0 L 1180 0 C 1110 240 990 460 828 596 L 0 596 Z"
          fill="url(#photoTone)"/>
    <path d="M1180 0 C 1110 240 990 460 828 596" fill="none" stroke="#ffffff" stroke-width="3" opacity=".85"/>
  </svg>

  <h1 class="headline">
    <span class="headline__script">Keep</span>
    <span class="headline__main">
      <span class="headline__white">HOPE</span><span class="headline__accent">RISING</span>
      <svg class="headline__chevrons" width="60" height="60" viewBox="0 0 60 60" aria-hidden="true">
        <path d="M4 8 L24 30 L4 52" fill="none" stroke="#8cf0f8" stroke-width="7" opacity=".8"/>
        <path d="M26 8 L46 30 L26 52" fill="none" stroke="#ffffff" stroke-width="7" opacity=".55"/>
      </svg>
    </span>
  </h1>

  <div class="signoff">
    <span class="signoff__text">From Corvalis TV Family</span>
  </div>
</main>
</body>
</html>
```